New Business Card Design Project

We require a business card design for Vexalund, a newly established Indian company.
Our focus is on the development, manufacturing, and export of a diverse array of pharmaceutical products on a global scale. The card should convey a professional appearance, as our primary markets are in Africa, China, and Southeast Asian nations.
We envision a two-sided business card, with the reverse side dedicated to a logo set against a solid color or an elegantly designed pattern. The corners should be rounded. We would appreciate seeing both horizontal and vertical design options. We trust the designer to utilize their expertise in creating this design.

The content for the business card is included in the attached Word file.

Target Market(s)

Our primary markets are in Africa, China, and Southeast Asian, Latin America, Maldives, Sri Lanka

Industry/Entity Type

Pharmaceutical Manufacturing and Export

Contact Information for Business Card

Colors

Designer to choose colors to be used in the design.

Requirements
Must have
• The reverse side of the business card features solely the logo along with the tagline, "Remedies of Life."
Should not have
• The logo should not exceed two instances, encompassing both the front and back sides of the card.

```html
<!DOCTYPE html>
<html lang="en">
<head>
<meta charset="UTF-8">
<title>Vexalund Business Card</title>
<link href="https://fonts.googleapis.com/css2?family=Poppins:wght@300;400;600;700&display=swap" rel="stylesheet">
<style>
  :root {
    --stage: #d6d6d6;
    --card: #222222;
    --brand-blue: #2aa7e0;
    --brand-coral: #f2614c;
    --ink-light: #f2f2f2;
    --ink-muted: #bdbdbd;
    --watermark-blue: #1f2b33;
    --watermark-coral: #332424;
  }
  html, body {
    margin: 0;
    padding: 0;
    width: 1200px;
    height: 1200px;
    overflow: hidden;
    background: var(--stage);
    font-family: "Poppins", sans-serif;
  }
  .stage {
    position: relative;
    width: 1200px;
    height: 1200px;
  }
  .card {
    position: absolute;
    top: 215px;
    width: 440px;
    height: 770px;
    background: var(--card);
    border-radius: 28px;
    box-shadow: 0 18px 40px rgba(0,0,0,0.28);
    overflow: hidden;
  }
  .card-front { left: 120px; }
  .card-back { left: 640px; }

  .front-watermark {
    position: absolute;
    left: 0;
    top: 0;
    width: 440px;
    height: 360px;
  }
  .watermark-circle {
    position: absolute;
    left: 230px;
    top: 40px;
    width: 170px;
    height: 170px;
    border-radius: 50%;
    background: var(--watermark-coral);
  }
  .watermark-name {
    position: absolute;
    left: 52px;
    top: 215px;
    margin: 0;
    font-weight: 600;
    font-size: 72px;
    line-height: 1;
    color: var(--watermark-blue);
    white-space: nowrap;
  }

  .identity {
    position: absolute;
    left: 52px;
    top: 372px;
    color: var(--ink-light);
  }
  .person-name {
    margin: 0;
    font-weight: 700;
    font-size: 31px;
    line-height: 1.1;
    color: var(--brand-blue);
    letter-spacing: 0.5px;
  }
  .person-role, .person-company {
    margin: 4px 0 0;
    font-weight: 300;
    font-size: 19px;
    line-height: 1.2;
  }
  .divider {
    width: 18px;
    height: 2px;
    background: var(--brand-blue);
    margin: 26px 0 26px;
  }
  .address {
    margin: 0;
    font-weight: 400;
    font-size: 18px;
    line-height: 1.5;
    font-style: normal;
  }
  .contact-list {
    list-style: none;
    margin: 0;
    padding: 0;
  }
  .contact-item {
    display: flex;
    align-items: center;
    gap: 12px;
    font-weight: 400;
    font-size: 18px;
    line-height: 1.9;
  }
  .contact-icon {
    width: 14px;
    height: 14px;
    flex: none;
    fill: var(--brand-coral);
  }

  .brand-lockup {
    position: absolute;
    left: 50%;
    top: 50%;
    transform: translate(-50%, -50%) rotate(-90deg);
    display: flex;
    flex-direction: column;
    align-items: flex-start;
    white-space: nowrap;
  }
  .brand-row {
    display: flex;
    align-items: center;
    gap: 22px;
  }
  .brand-dot {
    width: 34px;
    height: 34px;
    border-radius: 50%;
    background: var(--brand-coral);
  }
  .brand-name {
    font-weight: 600;
    font-size: 66px;
    line-height: 1.1;
    color: var(--brand-blue);
    letter-spacing: 1px;
  }
  .brand-tagline {
    margin: 6px 0 0 56px;
    font-weight: 300;
    font-size: 20px;
    letter-spacing: 3px;
    color: var(--ink-muted);
  }
</style>
</head>
<body>
<main class="stage">
  <section class="card card-front" aria-label="Card front">
    <div class="front-watermark" aria-hidden="true">
      <span class="watermark-circle"></span>
      <p class="watermark-name">Vexalund</p>
    </div>
    <div class="identity">
      <h1 class="person-name">Rohan K. Salvi</h1>
      <p class="person-role">CEO</p>
      <p class="person-company">Vexalund</p>
      <div class="divider"></div>
      <address class="address">12, Nilgiri Colony, 440021<br>Wardha, India</address>
      <div class="divider"></div>
      <ul class="contact-list">
        <li class="contact-item">
          <svg class="contact-icon" viewBox="0 0 16 16" aria-hidden="true"><path d="M3.5 1l2.5 3-1.5 2c1 2 2.5 3.5 4.5 4.5l2-1.5 3 2.5-1.5 3C6 14 2 10 .5 2.5z"/></svg>
          <span>+919876501234</span>
        </li>
        <li class="contact-item">
          <svg class="contact-icon" viewBox="0 0 16 16" aria-hidden="true"><path d="M1 3h14v10H1z M1.8 3.8L8 9l6.2-5.2" stroke="#222" stroke-width="1.2"/></svg>
          <span>rsalvi@vexalund.com</span>
        </li>
        <li class="contact-item">
          <svg class="contact-icon" viewBox="0 0 16 16" aria-hidden="true"><circle cx="8" cy="8" r="7"/><path d="M1 8h14M8 1c-3 3-3 11 0 14M8 1c3 3 3 11 0 14" stroke="#222" stroke-width="1" fill="none"/></svg>
          <span>www.vexalund.com</span>
        </li>
      </ul>
    </div>
  </section>

  <section class="card card-back" aria-label="Card back">
    <div class="brand-lockup">
      <div class="brand-row">
        <span class="brand-dot"></span>
        <span class="brand-name">Vexalund</span>
      </div>
      <p class="brand-tagline">Remedies of Life</p>
    </div>
  </section>
</main>
</body>
</html>
```